Professional Website

We are looking for a new website for our Staffing Company. Attached is a document with all the details and pages needed along with some examples of others websites.

We want a professional Look and feel around the same color theme as the attached Amber Compass.

We currently host our site on PageLoom.io. If the winning designer can also add to PageLoom, that is a plus.

```html
<!DOCTYPE html>
<html lang="en">
<head>
<meta charset="utf-8">
<title>WorkBridge Clerical &amp; Industrial</title>
<link href="https://fonts.googleapis.com/css2?family=Montserrat:wght@400;500;600;700&family=Lato:wght@400&display=swap" rel="stylesheet">
<style>
:root{
  --navy:#2b2b93;
  --ink:#111;
  --white:#fff;
  --text:#3c3c3c;
  --black:#000;
}
*{margin:0;padding:0;box-sizing:border-box}
html,body{width:762px;height:1200px;overflow:hidden;background:var(--white);font-family:'Montserrat',sans-serif}
.page{position:relative;width:762px;height:1200px}
.topbar{position:absolute;left:0;top:0;width:762px;height:43px;background:var(--navy)}
.brand{position:absolute;color:var(--white);font-weight:700;line-height:1}
.topbar .brand{left:83px;top:9px;font-size:19px}
.topbar .brand small{display:block;font-size:5px;font-weight:500;letter-spacing:.4px;margin-top:2px}
.hotline-top{position:absolute;left:298px;top:16px;color:var(--white);font-size:9px;font-weight:700}
.login{position:absolute;top:10px;height:24px;border:1px solid var(--white);color:var(--white);font-size:7.5px;font-weight:700;display:flex;align-items:center;justify-content:center}
.hero{position:absolute;left:0;top:43px;width:762px;height:407px;background:linear-gradient(100deg,#6f7f93 0%,#3d5d86 35%,#294a6e 65%,#7e8fa3 100%)}
.nav{position:absolute;top:61px;left:0;width:762px;font-size:8.5px;font-weight:700;color:var(--white)}
.nav span{position:absolute}
.nav .active{color:var(--navy)}
.hero-title{position:absolute;left:0;top:202px;width:762px;text-align:center;color:var(--white);font-size:33px;font-weight:700}
.btn-outline{position:absolute;border:1.5px solid var(--white);color:var(--white);font-weight:700;font-size:9.5px;display:flex;align-items:center;justify-content:center}
.cards{position:absolute;left:84px;top:343px;width:594px;height:342px;background:var(--white);box-shadow:0 2px 6px rgba(0,0,0,.12)}
.card{position:absolute;top:5px;width:289px;height:332px;color:var(--white);text-align:center}
.card.job{left:4px;background:linear-gradient(160deg,#a59c90 0%,#6a5840 45%,#1e2a3a 100%)}
.card.hire{left:301px;background:linear-gradient(160deg,#d9d9d6 0%,#8a8a88 45%,#2a2e34 100%)}
.card h2{position:absolute;top:187px;width:100%;font-size:12.5px;font-weight:700}
.card .rule{position:absolute;top:212px;left:122px;width:46px;height:2px;background:var(--white)}
.card p{position:absolute;top:223px;left:14px;right:14px;font-family:'Lato',sans-serif;font-size:8.6px;line-height:15px}
.intro{position:absolute;left:102px;top:725px;width:558px;font-size:12.6px;line-height:22px;color:var(--text);text-align:justify;text-align-last:center;letter-spacing:.2px}
.footer{position:absolute;left:0;top:901px;width:762px;height:299px;background:var(--black);color:var(--white)}
.footer .brand{left:71px;top:56px;font-size:33px}
.footer .brand small{display:block;font-size:8px;font-weight:500;letter-spacing:.8px;margin-top:2px}
.hotline-foot{position:absolute;left:96px;top:117px;font-size:10.5px;font-weight:600}
.social{position:absolute;top:175px;width:29px;height:29px;border-radius:50%;background:var(--navy)}
.col-title{position:absolute;left:282px;font-size:10px;font-weight:700}
.links{position:absolute;left:282px;list-style:none;font-size:8.8px;line-height:15.2px}
.field{position:absolute;background:var(--white);border-radius:4px;color:#666;font-size:7.5px;padding:11px 9px}
.submit{position:absolute;left:423px;top:1088px;width:95px;height:28px;background:var(--navy);border:1px solid var(--white);color:var(--white);font-size:9px;font-weight:700;display:flex;align-items:center;justify-content:center}
.divider{position:absolute;left:50px;top:1142px;width:662px;height:1px;background:#555}
.copyright{position:absolute;left:0;top:1160px;width:762px;text-align:center;color:var(--white);font-size:8.8px}
</style>
</head>
<body>
<div class="page">
  <header class="topbar">
    <div class="brand">WorkBridge<small>CLERICAL &amp; INDUSTRIAL</small></div>
    <div class="hotline-top">Hotline # 555-014-2290</div>
    <div class="login" style="left:415px;width:79px">Lakeshore Bank Login</div>
    <div class="login" style="left:500px;width:79px">QuickPay Card Login</div>
    <div class="login" style="left:586px;width:80px">Employee Login</div>
  </header>

  <section class="hero" role="img" aria-label="Photo of a smiling recruiter interviewing a candidate in a bright office"></section>
  <nav class="nav">
    <span class="active" style="left:115px">HOME</span>
    <span style="left:175px">LOOKING FOR A JOB</span>
    <span style="left:301px">LOOKING FOR EMPLOYEES</span>
    <span style="left:455px">OFFICE INFORMATION</span>
    <span style="left:588px">CONTACT US</span>
  </nav>
  <h1 class="hero-title">WorkBridge Clerical &amp; Industrial</h1>
  <div class="btn-outline" style="left:334px;top:256px;width:94px;height:28px">Get Started</div>

  <section class="cards">
    <article class="card job" role="img" aria-label="Photo of job seekers waiting for an interview">
      <h2>I'M LOOKING FOR A JOB</h2>
      <div class="rule"></div>
      <p>Lorem ipsum dolor sit amet, consectetur adipiscing elit, sed do eiusmod tempor incididunt ut labore et dolore magna aliqua. Quis ipsum suspendisse ultrices gravida.</p>
      <div class="btn-outline" style="left:97px;top:273px;width:94px;height:28px">Learn More</div>
    </article>
    <article class="card hire" role="img" aria-label="Photo of a cheering employee at her desk">
      <h2>I NEED EMPLOYEES</h2>
      <div class="rule"></div>
      <p>Lorem ipsum dolor sit amet, consectetur adipiscing elit, sed do eiusmod tempor incididunt ut labore et dolore magna aliqua. Quis ipsum suspendisse ultrices gravida.</p>
      <div class="btn-outline" style="left:97px;top:273px;width:94px;height:28px">Learn More</div>
    </article>
  </section>

  <p class="intro">Greatest part of our daily job is that we are constantly bringing people together. Our Clients come to us in search of the perfect candidate and the job hunters approach us when they are in need of a job or looking for their next exciting role. Being able to work with and connect the two is incredibly satisfying. Not to mention that in today's current job market, employers are fighting for the top talent. This makes our employees and partners grateful for the help in finding it!</p>

  <footer class="footer">
    <div class="brand">WorkBridge<small>CLERICAL &amp; INDUSTRIAL</small></div>
    <div class="hotline-foot">HOTLINE # 555-014-2290</div>
    <span class="social" style="left:85px"></span>
    <span class="social" style="left:126px"></span>
    <span class="social" style="left:167px"></span>
    <span class="social" style="left:209px"></span>
    <div class="col-title" style="top:32px">QUICK LINKS</div>
    <ul class="links" style="top:55px"><li>Home</li><li>Looking For A Job</li><li>Looking For Employees</li><li>Office Information</li><li>Contact Us</li></ul>
    <div class="col-title" style="top:159px">AREAS WE SERVICE</div>
    <ul class="links" style="top:182px"><li>North Ridgeview</li><li>Millbrook</li><li>Oak Hollow</li></ul>
  </footer>
  <div class="field" style="left:423px;top:932px;width:131px;height:30px">First Name</div>
  <div class="field" style="left:560px;top:932px;width:131px;height:30px">Last Name</div>
  <div class="field" style="left:423px;top:969px;width:131px;height:30px">Email Address</div>
  <div class="field" style="left:560px;top:969px;width:131px;height:30px">Phone Number</div>
  <div class="field" style="left:423px;top:1006px;width:268px;height:70px;padding-top:8px">Message</div>
  <div class="submit">SUBMIT</div>
  <div class="divider"></div>
  <div class="copyright">© Copyrights 2022 <b>WORKBRIDGE</b> &nbsp;| &nbsp; All Rights Reserved</div>
</div>
</body>
</html>
```